Business Card Design - Photographer

I am a landscape photographer and I require a business card design. 

I require two designs:
1)  a double sided business card
 and
b)  a single sided business card 

The single sided design can either be the same as the double sided (with just one side having all the information)....or it can be an entire new design. Its up to you.

My corporate colours are (CMYK):

Blue   69, 32, 0, 0
Grey  72,  64,  47,  31
Green  32,  2,  91,  0
Yellow   0, 19, 92, 0
Orange  0, 39, 75, 0

Colour space in final file should be in CMYK.

The details that need to be included on the card:

- Use the provided Logo
- Name: Wiktor Baranowski
- Email:   sales@vistalumeworks.com.au
- Website:    vistalumeworks.com.au
- Twitter:    twitter.com/vistalumeworks
- Facebook:   facebook.com/vistalumeworks
- Mobile  0417 539 662

Please use the attached template to design the logo to the specified size, including the marked bleed lines. I have also attached my logo in PNG (transparent background) and ai format for you to use.

The final file should be:
- Photoshop version with layers so I can edit the name/text etc. All non vector files should be high resolution at 1039 x 697 pixels at 300 dpi.

I also require a file as:
- Vector based PDF

Anyway questions please contact me.

Thank you

Industry/Entity Type

Landscape

Logo styles of interest
Pictorial/Combination Logo
Abstract Logo
Wordmark Logo
Lettermark Logo
Requirements
Must have
• The details that need to be included on the card:

- Use the provided Logo
- Name: Wiktor Baranowski
- Email: sales@vistalumeworks.com.au
- Website: vistalumeworks.com.au
- Twitter: twitter.com/vistalumeworks
- Facebook: facebook.com/vistalumeworks
- Mobile 0417 539 662

```html
<!DOCTYPE html>
<html lang="en">
<head>
<meta charset="utf-8">
<title>Vistalume Works – Business Cards</title>
<link rel="stylesheet" href="https://fonts.googleapis.com/css2?family=Cinzel:wght@500;600&family=Tinos:wght@400;700&family=Open+Sans:wght@400&display=swap">
<style>
  :root {
    --stage: #d9d4cc;
    --card: #ffffff;
    --ink-grey: #3d4252;
    --brand-blue: #3e8fd0;
    --text-grey: #444854;
    --rule: #c9c9c9;
    --on-dark: #ffffff;
  }
  * { margin: 0; padding: 0; box-sizing: border-box; }
  html, body { width: 1200px; height: 386px; overflow: hidden; }
  body { background: var(--stage); position: relative; }

  .card {
    position: absolute;
    top: 45px;
    width: 526px;
    height: 300px;
    background: var(--card);
    border-radius: 18px;
    overflow: hidden;
    box-shadow: 0 2px 6px rgba(0,0,0,.18);
  }
  .card--front { left: 55px; }
  .card--back  { left: 628px; }

  .brand { position: absolute; text-align: center; }
  .brand__mark {
    display: block;
    margin: 0 auto;
    border-radius: 50%;
    background: var(--ink-grey);
  }
  .brand__name {
    display: inline-block;
    font-family: "Cinzel", serif;
    font-weight: 500;
    color: var(--ink-grey);
    white-space: nowrap;
    letter-spacing: .5px;
    line-height: 1;
    border-bottom: 1.5px solid var(--ink-grey);
  }
  .brand__tagline {
    font-family: "Cinzel", serif;
    font-weight: 600;
    color: var(--ink-grey);
    white-space: nowrap;
    line-height: 1;
  }

  .card--front .brand { left: 20px; top: 62px; width: 240px; }
  .card--front .brand__mark { width: 84px; height: 84px; }
  .card--front .brand__name { font-size: 24px; margin-top: 18px; padding-bottom: 3px; }
  .card--front .brand__tagline { font-size: 9px; letter-spacing: 1.8px; margin-top: 5px; }

  .card--back .brand { left: 0; top: 55px; width: 526px; }
  .card--back .brand__mark { width: 96px; height: 96px; }
  .card--back .brand__name { font-size: 27px; margin-top: 12px; padding-bottom: 4px; }
  .card--back .brand__tagline { font-size: 10.5px; letter-spacing: 2.2px; margin-top: 7px; }

  .divider {
    position: absolute;
    left: 279px; top: 80px;
    width: 1px; height: 137px;
    background: var(--rule);
  }

  .contact {
    position: absolute;
    left: 298px; top: 62px;
    font-family: "Tinos", serif;
    font-size: 14px;
    color: var(--text-grey);
    line-height: 18px;
  }
  .contact__name {
    font-weight: 700;
    font-size: 15px;
    line-height: 20px;
    color: var(--ink-grey);
    margin-bottom: 6px;
  }
  .contact__address { margin-bottom: 14px; }
  .contact__item { display: flex; align-items: center; gap: 5px; }
  .contact__icon { width: 9px; height: 9px; flex: none; }

  .band { position: absolute; left: 0; bottom: 0; }
  .band__url {
    position: absolute;
    left: 276px; bottom: 11px;
    font-family: "Tinos", serif;
    font-size: 14px;
    letter-spacing: 1.4px;
    color: var(--on-dark);
  }

  .back-url {
    position: absolute;
    left: 0; top: 245px; width: 526px;
    text-align: center;
    font-family: "Open Sans", sans-serif;
    font-size: 13px;
    letter-spacing: 2.6px;
    color: var(--text-grey);
  }
</style>
</head>
<body>

<section class="card card--front">
  <div class="brand">
    <span class="brand__mark"></span>
    <div class="brand__name">VISTALUME WORKS</div>
    <div class="brand__tagline">FINE ART PHOTOGRAPHY</div>
  </div>

  <div class="divider"></div>

  <div class="contact">
    <p class="contact__name">Wiktor Baranowski</p>
    <p class="contact__address">00, Complex Name<br>State Name, City 0020</p>
    <p class="contact__item">
      <svg class="contact__icon" viewBox="0 0 9 9"><rect x="2" y="0" width="5" height="9" rx="1" fill="var(--text-grey)"/><rect x="3" y="1.2" width="3" height="5" fill="#fff"/></svg>
      0417 539 662
    </p>
    <p class="contact__item">
      <svg class="contact__icon" viewBox="0 0 9 9"><rect width="9" height="9" rx="1.5" fill="var(--brand-blue)"/></svg>
      vistalumeworks
    </p>
    <p class="contact__item">
      <svg class="contact__icon" viewBox="0 0 9 9"><rect width="9" height="9" rx="1.5" fill="var(--ink-grey)"/></svg>
      vistalumeworks
    </p>
    <p class="contact__item">
      <svg class="contact__icon" viewBox="0 0 9 9"><rect y="1.5" width="9" height="6" fill="var(--text-grey)"/><path d="M0 1.5 L4.5 5 L9 1.5" stroke="#fff" fill="none" stroke-width=".8"/></svg>
      sales@vistalumeworks.com.au
    </p>
  </div>

  <svg class="band" width="526" height="300" viewBox="0 0 526 300">
    <polygon points="0,257 249,257 241,271 0,271" fill="var(--brand-blue)"/>
    <polygon points="0,276 248,276 262,255 526,255 526,300 0,300" fill="var(--ink-grey)"/>
  </svg>
  <div class="band__url">www.vistalumeworks.com.au</div>
</section>

<section class="card card--back">
  <div class="brand">
    <span class="brand__mark"></span>
    <div class="brand__name">VISTALUME WORKS</div>
    <div class="brand__tagline">FINE ART PHOTOGRAPHY</div>
  </div>
  <div class="back-url">www.vistalumeworks.com.au</div>
</section>

</body>
</html>
```